Business Card Design For Marketing Agnecy LVP

Need business card design for marketing agency.

Doug Fenwick
President, CEO
1-555-302-4196
doug@boldpromoperksgroup.example
www.BoldPromoPerksGroup.example

Back Side:
Boost Sales Using Rewards, Incentives & Giveaways
Get A Free Sample Package

Target Market(s)

B2B

Industry/Entity Type

Marketing

Contact Information for Business Card

Doug Fenwick
President, CEO
1-555-302-4196

Back Side:
Get A Free Sample Package

Please note that my current url is OLD DESIGN. I am working on new design and want the business card to match color themes at least on new site. Here is the demo link for new site so you can see the colors I use, etc.

http://layoutcratehub.example/kq/doug/lvp_final/index.html

Requirements
Must have
• Please note that my current url is OLD DESIGN. I am working on new design and want the business card to match color themes at least on new site. Here is the demo link for new site so you can see the colors I use, etc.

Nice to have

Should not have

```html
<!DOCTYPE html>
<html lang="en">
<head>
<meta charset="utf-8">
<title>LVP Business Card</title>
<link href="https://fonts.googleapis.com/css2?family=Montserrat:wght@400;500;700;800&display=swap" rel="stylesheet">
<style>
  :root {
    --bg: #e4e4e2;
    --card: #2f3034;
    --blue: #1f7acb;
    --white: #f2f2f2;
    --muted: #d8d8d8;
  }
  * { box-sizing: border-box; margin: 0; padding: 0; }
  html, body { width: 1200px; height: 810px; overflow: hidden; }
  body {
    background: var(--bg);
    font-family: "Montserrat", sans-serif;
    display: flex;
    align-items: center;
    justify-content: center;
    gap: 40px;
  }
  .card {
    width: 540px;
    height: 308px;
    background: var(--card);
    border-bottom: 4px solid var(--blue);
    box-shadow: 0 10px 24px rgba(0,0,0,0.22);
    position: relative;
    color: var(--white);
  }
  .brand {
    display: flex;
    align-items: center;
    gap: 10px;
    color: var(--blue);
    font-weight: 800;
    letter-spacing: 2px;
  }
  .brand-dot {
    width: 14px; height: 14px;
    border-radius: 50%;
    background: var(--blue);
  }
  /* Front */
  .card-front .brand {
    position: absolute;
    left: 44px; top: 92px;
    font-size: 54px;
  }
  .divider {
    position: absolute;
    left: 212px; top: 62px;
    width: 2px; height: 120px;
    background: var(--blue);
  }
  .contact {
    position: absolute;
    left: 240px; top: 62px;
  }
  .contact-name {
    color: var(--blue);
    font-weight: 700;
    font-size: 19px;
  }
  .contact-title {
    font-size: 12px;
    font-weight: 500;
    margin-bottom: 18px;
  }
  .contact-list { list-style: none; }
  .contact-list li {
    display: flex;
    align-items: center;
    gap: 8px;
    font-size: 11.5px;
    line-height: 20px;
    color: var(--muted);
  }
  .contact-list svg { width: 11px; height: 11px; flex: none; }
  .tagline {
    position: absolute;
    left: 44px; bottom: 44px;
    font-size: 14px;
    font-weight: 500;
    color: var(--white);
  }
  /* Back */
  .card-back {
    display: flex;
    flex-direction: column;
    align-items: center;
    justify-content: center;
  }
  .card-back .brand {
    font-size: 72px;
    margin-bottom: 26px;
  }
  .card-back .brand-dot { width: 18px; height: 18px; }
  .offer {
    color: var(--blue);
    font-weight: 800;
    font-size: 24px;
    letter-spacing: 0.5px;
  }
  .site {
    margin-top: 6px;
    font-size: 14px;
    font-weight: 500;
    color: var(--white);
  }
  .site b { font-weight: 700; }
</style>
</head>
<body>
  <section class="card card-front">
    <div class="brand"><span class="brand-dot"></span>LVP</div>
    <div class="divider"></div>
    <div class="contact">
      <p class="contact-name">Doug Fenwick</p>
      <p class="contact-title">President, CEO</p>
      <ul class="contact-list">
        <li>
          <svg viewBox="0 0 12 12"><circle cx="6" cy="6" r="5.5" fill="none" stroke="#1f7acb"/><path d="M4 3.5l1 1-0.6 0.8a4 4 0 0 0 2.3 2.3l0.8-0.6 1 1-0.8 0.8C5.5 8.6 3.4 6.5 3.2 4.3z" fill="#1f7acb"/></svg>
          1-555-302-4196
        </li>
        <li>
          <svg viewBox="0 0 12 12"><rect x="1" y="2.5" width="10" height="7" fill="#1f7acb"/><path d="M1 2.5l5 4 5-4" fill="none" stroke="#2f3034" stroke-width="1"/></svg>
          doug@boldpromoperksgroup.example
        </li>
        <li>
          <svg viewBox="0 0 12 12"><circle cx="6" cy="6" r="5" fill="none" stroke="#1f7acb" stroke-width="1.2"/><path d="M1 6h10M6 1c-2.5 3-2.5 7 0 10M6 1c2.5 3 2.5 7 0 10" fill="none" stroke="#1f7acb" stroke-width="0.9"/></svg>
          www.BoldPromoPerksGroup.example
        </li>
      </ul>
    </div>
    <p class="tagline">Boost Sales Using Rewards, Incentives &amp; Giveaways</p>
  </section>

  <section class="card card-back">
    <div class="brand"><span class="brand-dot"></span>LVP</div>
    <p class="offer">GET A FREE SAMPLE PACKAGE</p>
    <p class="site">www.<b>BoldPromoPerksGroup</b>.example</p>
  </section>
</body>
</html>
```